Moravel Aesthetic Doctor

I require an elegant, luxurious looking business card for my aesthetic business. I am a doctor and that will set me aside from competitors. I am planning to provide home and spa based treatments to clients with high expectations. I have attached my logo.

```html
<!DOCTYPE html>
<html lang="en">
<head>
<meta charset="utf-8">
<title>Moravel Aesthetic Doctor — Business Card</title>
<link href="https://fonts.googleapis.com/css2?family=Marcellus&family=Roboto:wght@300;400&family=Montserrat:wght@400&display=swap" rel="stylesheet">
<style>
  :root {
    --backdrop: #d9dadb;
    --blue-light: #4ba8df;
    --blue-deep: #0e5ea6;
    --blue-accent: #4aa3dc;
    --band-grey: #9aa2ab;
    --card-white: #f4f5f6;
    --card-silver: #e4e6e8;
    --ink: #3d4247;
    --icon-bg: #e3e6ea;
    --white: #ffffff;
  }
  * { box-sizing: border-box; margin: 0; padding: 0; }
  html, body { width: 1200px; height: 576px; overflow: hidden; }
  body { background: var(--backdrop); position: relative; font-family: "Roboto", sans-serif; }

  .card { position: absolute; top: 138px; border-radius: 12px; overflow: hidden; }

  /* Front */
  .card--front {
    left: 82px; width: 484px; height: 294px;
    background: linear-gradient(160deg, var(--blue-light) 0%, #2a86cb 45%, var(--blue-deep) 100%);
  }
  .brand-mark { position: absolute; border-radius: 50%; }
  .card--front .brand-mark { left: 62px; top: 46px; width: 104px; height: 104px; border: 2px solid rgba(255,255,255,.85); }
  .wordmark { position: absolute; font-family: "Marcellus", serif; font-weight: 400; line-height: 1; white-space: nowrap; }
  .wordmark__name { display: block; font-size: 46px; letter-spacing: 1px; }
  .wordmark__role { display: block; font-size: 21px; letter-spacing: 1.5px; margin-top: 12px; }
  .card--front .wordmark { left: 182px; top: 60px; color: var(--white); }

  .services {
    position: absolute; left: 0; right: 0; top: 196px;
    text-align: center; color: var(--white); font-size: 13px; line-height: 18px; font-weight: 400;
    white-space: nowrap;
  }
  .services .sep { margin: 0 8px; }
  .treatment-band {
    position: absolute; left: 0; right: 0; top: 245px; height: 25px;
    background: var(--band-grey); color: var(--white);
    font-family: "Montserrat", sans-serif; font-size: 12.5px; letter-spacing: 1px;
    display: flex; align-items: center; justify-content: center; white-space: nowrap;
  }

  /* Back */
  .card--back {
    left: 603px; width: 480px; height: 292px;
    background: linear-gradient(180deg, var(--card-white) 0%, var(--card-silver) 100%);
  }
  .side-strip { position: absolute; left: 0; top: 0; bottom: 0; width: 38px; background: var(--blue-accent); }
  .side-rule { position: absolute; left: 42px; top: 0; bottom: 0; width: 2px; background: var(--blue-accent); }
  .card--back .brand-mark { left: 72px; top: 36px; width: 88px; height: 88px; border: 2px solid #9aa2ab; }
  .card--back .wordmark { left: 177px; top: 48px; color: var(--blue-accent); }
  .card--back .wordmark__name { font-size: 44px; }
  .card--back .wordmark__role { font-size: 19px; margin-top: 8px; }

  .doctor { position: absolute; left: 67px; top: 198px; color: var(--ink); white-space: nowrap; }
  .doctor__name { font-size: 20px; font-weight: 300; }
  .doctor__letters { font-size: 10.5px; color: var(--blue-accent); margin-left: 4px; }
  .doctor__diploma { font-size: 13px; color: var(--blue-accent); margin-top: 3px; }
  .name-rule { position: absolute; left: 268px; top: 208px; width: 140px; height: 1px; background: #9aa2ab; }
  .social-pill {
    position: absolute; left: 405px; top: 199px; width: 75px; height: 19px;
    background: var(--blue-accent); border-radius: 10px 0 0 10px;
    display: flex; align-items: center; gap: 5px; padding-left: 10px;
  }
  .social-pill span { width: 11px; height: 11px; border-radius: 50%; background: var(--white); }

  .contacts {
    position: absolute; left: 67px; top: 240px;
    display: flex; gap: 10px; align-items: center; white-space: nowrap;
  }
  .contact { display: flex; align-items: center; gap: 5px; font-size: 12px; color: var(--ink); white-space: nowrap; flex: none; }
  .contact svg { width: 17px; height: 17px; flex: none; }
  .contact .accent { color: var(--blue-accent); }
</style>
</head>
<body>
  <section class="card card--front">
    <div class="brand-mark"></div>
    <div class="wordmark">
      <span class="wordmark__name">MORAVEL</span>
      <span class="wordmark__role">AESTHETIC DOCTOR</span>
    </div>
    <div class="services">
      <div>Dermal Injectables<span class="sep">|</span>Plasma Facials<span class="sep">|</span>Microneedling</div>
      <div>Skin Boosters<span class="sep">|</span>Excessive Sweating</div>
    </div>
    <div class="treatment-band">HOME AND SPA BASED TREATMENTS</div>
  </section>

  <section class="card card--back">
    <div class="side-strip"></div>
    <div class="side-rule"></div>
    <div class="brand-mark"></div>
    <div class="wordmark">
      <span class="wordmark__name">MORAVEL</span>
      <span class="wordmark__role">AESTHETIC DOCTOR</span>
    </div>

    <div class="doctor">
      <div><span class="doctor__name">Dr Elise Varden</span><span class="doctor__letters">MRCPCH MD</span></div>
      <div class="doctor__diploma">Australasian Diploma of Aesthetic Medicine</div>
    </div>
    <div class="name-rule"></div>
    <div class="social-pill" aria-label="Social profiles"><span></span><span></span></div>

    <div class="contacts">
      <div class="contact">
        <svg viewBox="0 0 20 20" aria-hidden="true"><circle cx="10" cy="10" r="10" fill="var(--icon-bg)"/><path d="M7 5.5c.6-.3 1.1 0 1.3.5l.6 1.5c.2.4 0 .8-.3 1l-.6.5c.5 1.1 1.3 1.9 2.4 2.4l.5-.6c.3-.3.7-.5 1-.3l1.5.6c.5.2.8.7.5 1.3-.4.9-1.2 1.4-2.1 1.2C9 13 7 11 6.4 8.2c-.2-.9.2-1.9.6-2.7z" fill="var(--blue-accent)"/></svg>
        <span>0800 555 019</span>
      </div>
      <div class="contact">
        <svg viewBox="0 0 20 20" aria-hidden="true"><circle cx="10" cy="10" r="10" fill="var(--icon-bg)"/><rect x="5" y="6.5" width="10" height="7" rx="1" fill="var(--blue-accent)"/><path d="M5.4 7l4.6 3.6L14.6 7" stroke="var(--white)" stroke-width="1" fill="none"/></svg>
        <span>elise@moravel.co.nz</span>
      </div>
      <div class="contact">
        <svg viewBox="0 0 20 20" aria-hidden="true"><circle cx="10" cy="10" r="10" fill="var(--icon-bg)"/><g stroke="var(--blue-accent)" stroke-width="1" fill="none"><circle cx="10" cy="10" r="5"/><ellipse cx="10" cy="10" rx="2.2" ry="5"/><path d="M5 10h10"/></g></svg>
        <span>www.<span class="accent">moravel</span>.co.nz</span>
      </div>
    </div>
  </section>
</body>
</html>
```